Business card design Needed for new logo / Construction business, home extensions and new builds

We need a business card design using our new logo files which i will attach to this project :)

We are a small construction business specialising in home extensions, new builds and property development. We are very ambitious and would appreciate professional and elegant designs for our new business card.

Very serious about using the services on MakerQuarry and recently acquired our new logo from here :)

Please get involved, i will feedback when i can as i am very busy but can respond daily, thanks

Target Market(s)

People that want to build onto their houses, new building developments or adding too their existing property

Industry/Entity Type

Construction

Contact Information for Business Card

Renwick Tolliver Construction, Lionel Ashby (Managing Director), Tel 07822254961, email - info@renwick-tolliver, www.renwick-tolliver.co.uk

Colors

Designer to choose colors to be used in the design.

Requirements
Must have
• I like a deep grey on the back please. A lot of you have provided black from and back, try mixing things up a little. The black looks cool 😎 Thanks

```html
<!DOCTYPE html>
<html lang="en">
<head>
<meta charset="utf-8">
<title>Renwick Tolliver Construction – Business Card</title>
<link href="https://fonts.googleapis.com/css2?family=Cinzel:wght@500&family=Montserrat:wght@400&display=swap" rel="stylesheet">
<style>
  :root {
    --backdrop: #d9d9d7;
    --card-white: #ffffff;
    --card-grey: #666666;
    --gold: #c9962c;
    --gold-light: #f4cf7a;
    --silver: #a9acb0;
    --ink: #3a3a3a;
  }
  * { margin: 0; padding: 0; box-sizing: border-box; }
  html, body {
    width: 1200px; height: 801px; overflow: hidden;
    background: var(--backdrop);
  }
  .stage {
    width: 1200px; height: 801px;
    display: flex; align-items: center; justify-content: center; gap: 50px;
  }
  .card {
    width: 530px; height: 343px;
    border-radius: 3px;
    border-bottom: 4px solid var(--gold);
    border-right: 2px solid var(--gold);
    position: relative;
    box-shadow: 0 12px 28px rgba(0,0,0,0.18);
  }
  .card--front { background: var(--card-white); }
  .card--back { background: var(--card-grey); }

  /* front */
  .brand-mark {
    position: absolute; right: 70px; top: 58px;
    width: 118px; height: 118px;
    background: linear-gradient(135deg, var(--gold) 0%, var(--gold-light) 50%, var(--gold) 100%);
  }
  .front-info { position: absolute; left: 44px; top: 48px; }
  .company-name {
    font-family: "Cinzel", serif; font-weight: 500;
    color: var(--silver); font-size: 21px; line-height: 1.15; letter-spacing: 1px;
  }
  .company-name span { display: block; }
  .person { margin-top: 38px; }
  .person-name {
    font-family: "Cinzel", serif; font-weight: 500;
    color: var(--gold); font-size: 21px; letter-spacing: 1px;
  }
  .person-role {
    font-family: "Montserrat", sans-serif; color: var(--ink); font-size: 13px; margin-top: 2px;
  }
  .contact-list { list-style: none; margin-top: 28px; }
  .contact-list li {
    display: flex; align-items: center; gap: 9px;
    font-family: "Montserrat", sans-serif; color: var(--ink); font-size: 13px;
    margin-bottom: 7px;
  }
  .contact-list svg { width: 12px; height: 12px; fill: none; stroke: var(--gold); stroke-width: 2; }

  /* back */
  .back-lockup {
    position: absolute; inset: 0;
    display: flex; flex-direction: column; align-items: center; justify-content: center;
  }
  .back-mark {
    width: 70px; height: 70px; margin-bottom: 22px;
    background: linear-gradient(135deg, var(--gold) 0%, var(--gold-light) 50%, var(--gold) 100%);
  }
  .back-name {
    font-family: "Cinzel", serif; font-weight: 500; color: var(--gold);
    text-align: center; letter-spacing: 1.5px;
  }
  .back-name .line-main { display: block; font-size: 27px; }
  .back-name .line-sub { display: block; font-size: 17px; margin-top: 2px; letter-spacing: 3px; }
</style>
</head>
<body>
<main class="stage">
  <section class="card card--front">
    <div class="brand-mark" aria-hidden="true"></div>
    <div class="front-info">
      <p class="company-name"><span>Renwick Tolliver</span><span>Construction</span></p>
      <div class="person">
        <p class="person-name">Lionel Ashby</p>
        <p class="person-role">Managing Director</p>
      </div>
      <ul class="contact-list">
        <li>
          <svg viewBox="0 0 24 24"><path d="M5 3h4l2 5-3 2a12 12 0 0 0 6 6l2-3 5 2v4a2 2 0 0 1-2 2A18 18 0 0 1 3 5a2 2 0 0 1 2-2z"/></svg>
          07822254961
        </li>
        <li>
          <svg viewBox="0 0 24 24"><rect x="3" y="5" width="18" height="14" rx="1"/><path d="M3 6l9 7 9-7"/></svg>
          info@renwick-tolliver
        </li>
        <li>
          <svg viewBox="0 0 24 24"><circle cx="12" cy="12" r="9"/><path d="M3 12h18M12 3a14 14 0 0 1 0 18M12 3a14 14 0 0 0 0 18"/></svg>
          www.renwick-tolliver.co.uk
        </li>
      </ul>
    </div>
  </section>

  <section class="card card--back">
    <div class="back-lockup">
      <div class="back-mark" aria-hidden="true"></div>
      <p class="back-name">
        <span class="line-main">Renwick Tolliver</span>
        <span class="line-sub">Construction</span>
      </p>
    </div>
  </section>
</main>
</body>
</html>
```